Modern Business Card

Modern professional business card with more than just logo and demographic info. Something memorable.

We are a trendy/modern chiropractic group with an emphasis on neurology, hence the minimalist-type brain logo. We want to convey that modern and technical aspect with professionalism and the elite nature of our practice environment.

```html
<!DOCTYPE html>
<html lang="en">
<head>
<meta charset="utf-8">
<title>Keystone Chiropractic – Business Card</title>
<link rel="stylesheet" href="https://fonts.googleapis.com/css2?family=Cinzel:wght@400&family=Open+Sans:wght@400;600&display=swap">
<style>
  :root {
    --page: #2b2b2d;
    --card-black: #141416;
    --card-black-2: #1d1e21;
    --mark-grey: #3a3b3f;
    --brand-blue: #3d6fd4;
    --text-white: #f2f2f2;
    --text-grey: #a9abb0;
    --strip-white: #e9e9ea;
  }
  * { margin: 0; padding: 0; box-sizing: border-box; }
  html, body { width: 800px; height: 1200px; overflow: hidden; }
  body {
    background: var(--page);
    font-family: "Open Sans", Arial, sans-serif;
    position: relative;
  }
  .card {
    position: absolute;
    left: 80px;
    width: 640px;
    height: 366px;
    border-radius: 4px;
    overflow: hidden;
    box-shadow: 0 10px 30px rgba(0,0,0,.45);
  }
  /* Front side */
  .card-front {
    top: 150px;
    background: var(--card-black);
    display: flex;
    align-items: center;
    justify-content: center;
    gap: 18px;
  }
  .front-square {
    width: 34px; height: 34px;
    background: var(--mark-grey);
  }
  .front-name {
    font-family: "Cinzel", Georgia, serif;
    font-weight: 400;
    font-size: 40px;
    letter-spacing: 2px;
    color: var(--mark-grey);
    line-height: 1;
  }
  /* Back side */
  .card-back {
    top: 660px;
    background: linear-gradient(120deg, var(--card-black) 0%, var(--card-black-2) 100%);
    color: var(--text-white);
  }
  .brand {
    position: absolute;
    left: 40px; top: 58px;
    display: flex;
    align-items: center;
    gap: 14px;
  }
  .brand-square { width: 34px; height: 34px; background: var(--brand-blue); }
  .brand-name {
    font-family: "Cinzel", Georgia, serif;
    font-weight: 400;
    color: var(--text-white);
    line-height: 1;
  }
  .brand-name .line-1 { display: block; font-size: 38px; letter-spacing: 1px; }
  .brand-name .line-2 { display: block; font-size: 21px; letter-spacing: 1px; margin-top: 2px; }
  .person { position: absolute; left: 40px; top: 168px; }
  .person-name { color: var(--brand-blue); font-size: 19px; font-weight: 600; }
  .person-title { color: var(--text-grey); font-size: 12px; margin-top: 2px; }
  .address {
    position: absolute; left: 40px; top: 236px;
    font-size: 12.5px; line-height: 1.45; color: var(--text-white);
    font-style: normal;
  }
  .contacts {
    position: absolute; left: 372px; top: 166px;
    list-style: none; font-size: 12.5px;
  }
  .contacts li { display: flex; align-items: center; gap: 10px; height: 24px; }
  .contacts svg { width: 13px; height: 13px; fill: var(--brand-blue); flex: none; }
  .bands { position: absolute; left: 0; top: 0; width: 640px; height: 366px; }
  .legal {
    position: absolute; left: 352px; top: 326px;
    font-size: 13px; color: var(--text-white);
  }
</style>
</head>
<body>

<section class="card card-front" aria-label="Card front">
  <span class="front-square"></span>
  <span class="front-name">KEYSTONE</span>
</section>

<section class="card card-back" aria-label="Card back">
  <svg class="bands" viewBox="0 0 640 366" aria-hidden="true">
    <polygon points="0,328 300,328 294,336 0,336" fill="var(--strip-white)"/>
    <polygon points="318,316 640,316 640,352 290,352" fill="var(--brand-blue)"/>
  </svg>

  <div class="brand">
    <span class="brand-square"></span>
    <span class="brand-name"><span class="line-1">KEYSTONE</span><span class="line-2">CHIROPRACTIC</span></span>
  </div>

  <div class="person">
    <p class="person-name">Marcus Hale</p>
    <p class="person-title">Managing Director</p>
  </div>

  <address class="address">118 Harbor Lane, Lakeview,<br>Fairmont, US 40210</address>

  <ul class="contacts">
    <li>
      <svg viewBox="0 0 16 16"><path d="M3.5 1l2.6 3.2-1.4 1.6c.9 2 2.6 3.7 4.6 4.6l1.6-1.4L14 11.6 12.4 14C6.6 14 2 9.4 2 3.6z"/></svg>
      555-204-7788
    </li>
    <li>
      <svg viewBox="0 0 16 16"><path d="M1 3h14v10H1z M2 4.2v.6l6 4 6-4v-.6z" fill-rule="evenodd"/></svg>
      marcus@keystonechiro.com
    </li>
    <li>
      <svg viewBox="0 0 16 16"><path d="M8 1a5 5 0 0 0-5 5c0 3.6 5 9 5 9s5-5.4 5-9a5 5 0 0 0-5-5zm0 7a2 2 0 1 1 0-4 2 2 0 0 1 0 4z"/></svg>
      www.keystonechiro.com
    </li>
  </ul>

  <p class="legal">Keystone Chiropractic, LLC</p>
</section>

</body>
</html>
```